Brell Stone Company Business Cards

Front and Back Business Card - logo and text setup - cool design. I need workable photoshop or illustrator files so I can setup each employee card with design that is created
Updates

Hi everyone, thank you for the great entries. Please no more white and blue cards - there are so many already - black and silver only now please. thanks!

Target Market(s)

Construction Industry - Facility Managers

Industry/Entity Type

Construction

Contact Information for Business Card

I really like contemporary simplistic looks - clean neat....not opposed to seeing some black backrounds

Requirements
Must have
• Logo/website address with design on front only - www.brellstone-example.com (logo attached)
• Back:
• Name/Title/Company Address/Phone/email address
Nice to have
• Cool design
Should not have
• Nothing gimmicky like Fire or Water - since we are a Fire Protection company - it has all been done

```html
<!DOCTYPE html>
<html lang="en">
<head>
<meta charset="utf-8">
<title>Brell Stone Company – Business Cards</title>
<link href="https://fonts.googleapis.com/css2?family=Lato:wght@400;700;900&display=swap" rel="stylesheet">
<style>
  :root {
    --backdrop: #c9c9c9;
    --navy: #24427a;
    --charcoal: #232323;
    --orange: #ef4a32;
    --white: #ffffff;
    --light-text: #f2f2f2;
  }
  * { box-sizing: border-box; margin: 0; padding: 0; }
  html, body {
    width: 1200px; height: 1200px; overflow: hidden;
    background: var(--backdrop);
    font-family: "Lato", Arial, sans-serif;
  }
  .card {
    position: absolute;
    left: 250px;
    width: 708px;
    height: 404px;
    box-shadow: 0 6px 14px rgba(0,0,0,0.25);
  }
  .card-front { top: 144px; background: var(--navy); }
  .card-back { top: 582px; background: var(--charcoal); color: var(--light-text); }

  .brand-name {
    font-weight: 900;
    letter-spacing: -1px;
    white-space: nowrap;
    display: flex;
    align-items: center;
    gap: 14px;
  }
  .brand-mark { width: 18px; height: 18px; background: var(--orange); }

  .card-front .brand-name {
    position: absolute;
    left: 0; right: 0; top: 155px;
    justify-content: center;
    font-size: 66px;
    color: var(--white);
  }
  .front-url {
    position: absolute;
    left: 0; right: 0; top: 344px;
    text-align: center;
    font-size: 21px;
    color: var(--white);
  }
  .accent { color: var(--orange); }

  .card-back .brand-name {
    position: absolute;
    right: 42px; top: 50px;
    font-size: 54px;
    color: var(--orange);
  }
  .holder-name {
    position: absolute;
    left: 38px; top: 220px;
    font-size: 22px; font-weight: 700;
  }
  .holder-name .first { color: var(--navy); }
  .holder-name .last { color: var(--orange); }
  .holder-title {
    position: absolute;
    left: 38px; top: 248px;
    font-size: 16px;
  }
  .divider {
    position: absolute;
    left: 112px; top: 261px;
    width: 554px; height: 2px;
    background: var(--orange);
  }
  .contact-list {
    position: absolute;
    left: 38px; top: 284px;
    list-style: none;
    font-size: 16px;
    line-height: 21.3px;
  }
  .contact-list li { display: flex; align-items: center; gap: 9px; }
  .contact-list svg { width: 13px; height: 13px; fill: var(--orange); flex: none; }
  .address {
    position: absolute;
    right: 42px; top: 327px;
    text-align: right;
    font-size: 16px;
    line-height: 20px;
  }
</style>
</head>
<body>
  <section class="card card-front">
    <div class="brand-name"><span class="brand-mark"></span>Brell Stone</div>
    <p class="front-url">www.<span class="accent">brellstone-example</span>.com</p>
  </section>

  <section class="card card-back">
    <div class="brand-name">Brell Stone</div>
    <p class="holder-name"><span class="first">Dana</span> <span class="last">Whitlock</span></p>
    <p class="holder-title">Director</p>
    <div class="divider"></div>
    <ul class="contact-list">
      <li>
        <svg viewBox="0 0 16 16"><path d="M3.5 1l2.5 3-1.5 1.6c.8 1.9 2.3 3.4 4.2 4.3L10.3 8.4 13.5 11l-1.6 2.6C6.5 13.8 2 9.3 1.6 3.2z"/></svg>
        (555) 010-4821
      </li>
      <li>
        <svg viewBox="0 0 16 16"><path d="M4 1h8v4H4zM1 6h14v6h-3v3H4v-3H1zm4 4v4h6v-4z"/></svg>
        (555) 010-4822
      </li>
      <li>
        <svg viewBox="0 0 16 16"><path d="M1 3h14v10H1zm1.5 1.3v.4L8 8.6l5.5-3.9v-.4zM2.5 6.3v5.2h11V6.3L8 10.2z"/></svg>
        info@brellstone-example.com
      </li>
      <li>
        <svg viewBox="0 0 16 16"><path d="M8 1a7 7 0 100 14A7 7 0 008 1zm0 1.3c.8.8 1.4 2.1 1.6 3.7H6.4C6.6 4.4 7.2 3.1 8 2.3zM2.4 7.3h2.7c0 .5 0 1 .1 1.4H2.4a5.6 5.6 0 010-1.4zm4 0h3.2a8 8 0 010 1.4H6.4a8 8 0 010-1.4zm4.5 0h2.7a5.6 5.6 0 010 1.4h-2.7c.1-.4.1-.9 0-1.4zM6.4 10h3.2c-.2 1.6-.8 2.9-1.6 3.7-.8-.8-1.4-2.1-1.6-3.7z"/></svg>
        www.<span class="accent">brellstone-example</span>.com
      </li>
    </ul>
    <p class="address">48 Quarry Lane<br>Millbrook, NY 10000</p>
  </section>
</body>
</html>
```